BOLD & MINIMALIST DESIGN NEEDED

We want a very bold but minimalistic business card design that is impactful and utilizes both sides of the business card. Our current logo is included for your use.

We want bold fonts and good use of negative space. We don't want the logo to overpower the design.

Target Market(s)

Professionals who are building new commercial buildings.

Industry/Entity Type

Construction

Contact Information for Business Card

Name, Title, email, office phone, cell phone, website

Font styles to use
Serif
Sans Serif

Requirements
Must have
• Bold design!

```html
<!DOCTYPE html>
<html lang="en">
<head>
<meta charset="utf-8">
<title>Ridgeline Design + Build — Business Card</title>
<link rel="stylesheet" href="https://fonts.googleapis.com/css2?family=Montserrat:wght@400;500;800&family=Oswald:wght@600&display=swap">
<style>
  :root {
    --stage: #1c1c1c;
    --card: #262626;
    --card-light: #2f2f2f;
    --accent: #7cc42a;
    --ink: #ffffff;
    --emboss: #3c3c3c;
  }
  * { margin: 0; padding: 0; box-sizing: border-box; }
  html, body { width: 1200px; height: 900px; overflow: hidden; background: var(--stage); }
  .canvas { position: relative; width: 1200px; height: 900px; background: var(--stage); }

  .card {
    position: absolute;
    left: 250px;
    width: 700px;
    height: 400px;
    background: linear-gradient(135deg, var(--card) 0%, var(--card-light) 60%, var(--card) 100%);
    border-bottom: 6px solid var(--accent);
    box-shadow: 0 12px 30px rgba(0,0,0,.55);
    font-family: "Montserrat", sans-serif;
    color: var(--ink);
  }
  .card--front { top: 30px; }
  .card--back { top: 470px; }

  .brand { text-align: center; font-weight: 800; line-height: 1; }
  .brand__name { display: block; letter-spacing: 2px; }
  .brand__tag { display: block; letter-spacing: 8px; margin-top: 8px; }

  .card--front .brand {
    position: absolute; left: 0; right: 0; top: 150px;
    color: var(--emboss);
  }
  .card--front .brand__name { font-size: 64px; }
  .card--front .brand__tag { font-size: 17px; }

  .card--back .brand {
    position: absolute; left: 0; right: 0; top: 78px;
    color: var(--ink);
  }
  .card--back .brand__name { font-size: 40px; }
  .card--back .brand__tag { font-size: 12px; letter-spacing: 6px; }

  .person {
    position: absolute; top: 200px; right: 380px;
    text-align: right;
  }
  .person__name {
    font-family: "Oswald", sans-serif; font-weight: 600;
    font-size: 40px; color: var(--accent); line-height: 1; letter-spacing: .5px;
  }
  .person__title { font-size: 18px; font-weight: 400; margin-top: 4px; letter-spacing: 1px; }

  .divider {
    position: absolute; left: 340px; top: 204px;
    width: 2px; height: 66px; background: var(--accent);
  }

  .contacts {
    position: absolute; left: 358px; top: 204px;
    list-style: none; font-size: 17px; font-weight: 500;
  }
  .contacts li { display: flex; align-items: center; gap: 8px; height: 22px; letter-spacing: .5px; }
  .contacts svg { width: 15px; height: 15px; flex: none; }

  .website {
    position: absolute; left: 0; right: 0; top: 318px;
    text-align: center; font-size: 20px; font-weight: 500; letter-spacing: 2px;
  }
  .website__domain { color: var(--accent); }
</style>
</head>
<body>
<main class="canvas">

  <section class="card card--front" aria-label="Card front">
    <div class="brand">
      <span class="brand__name">RIDGELINE</span>
      <span class="brand__tag">DESIGN + BUILD</span>
    </div>
  </section>

  <section class="card card--back" aria-label="Card back">
    <div class="brand">
      <span class="brand__name">RIDGELINE</span>
      <span class="brand__tag">DESIGN + BUILD</span>
    </div>

    <div class="person">
      <p class="person__name">MARCUS HALLORAN</p>
      <p class="person__title">OWNER</p>
    </div>

    <div class="divider"></div>

    <ul class="contacts">
      <li>
        <svg viewBox="0 0 24 24" aria-hidden="true"><path fill="var(--accent)" d="M6.6 10.8a15.1 15.1 0 0 0 6.6 6.6l2.2-2.2a1 1 0 0 1 1-.25 11.4 11.4 0 0 0 3.6.57 1 1 0 0 1 1 1V20a1 1 0 0 1-1 1A17 17 0 0 1 3 4a1 1 0 0 1 1-1h3.5a1 1 0 0 1 1 1c0 1.25.2 2.45.57 3.57a1 1 0 0 1-.25 1z"/></svg>
        (555) 014-2286
      </li>
      <li>
        <svg viewBox="0 0 24 24" aria-hidden="true"><path fill="var(--accent)" d="M3 9c0-2 4-4 9-4s9 2 9 4v2h-4V9.5c-1.3-.6-3-.9-5-.9s-3.7.3-5 .9V11H3z"/><rect x="5" y="12" width="14" height="8" rx="1.5" fill="var(--accent)"/><circle cx="12" cy="16" r="2" fill="var(--card)"/></svg>
        (555) 014-2287
      </li>
      <li>
        <svg viewBox="0 0 24 24" aria-hidden="true"><rect x="2.5" y="5" width="19" height="14" rx="1" fill="none" stroke="var(--accent)" stroke-width="2"/><path d="M3 6l9 7 9-7" fill="none" stroke="var(--accent)" stroke-width="2"/></svg>
        ridgelinebuild@mail.com
      </li>
    </ul>

    <p class="website">www.<span class="website__domain">ridgelinebuild</span>.com</p>
  </section>

</main>
</body>
</html>
```